Letter and Envelope Design For Harborline Realty

Please design a letter and an envelope incorporating our logo (See Attached). We are also launched a business card contest. Since we want them to match, please feel free to submit a design for both the business card and also the letter design and envelope.

Requirements
Must have
• The envelope, the letter and the business cards must match somehow connecting the designs. We want them to have something that holds them together besides the logo.

```html
<!DOCTYPE html>
<html lang="en">
<head>
<meta charset="utf-8">
<title>Harborline Realty – Stationery</title>
<link href="https://fonts.googleapis.com/css2?family=Josefin+Sans:wght@600&family=Source+Sans+3:wght@400;600&display=swap" rel="stylesheet">
<style>
  :root{
    --navy:#283179;
    --ink:#4d4d4d;
    --paper:#ffffff;
    --backdrop:#d6d6d6;
  }
  *{margin:0;padding:0;box-sizing:border-box}
  html,body{width:1200px;height:1200px;overflow:hidden;background:var(--backdrop)}
  body{position:relative;font-family:"Source Sans 3",sans-serif;color:var(--paper)}
  .sheet,.card,.envelope{position:absolute;overflow:hidden}
  svg{position:absolute;left:0;top:0;display:block}
  .brand{position:absolute;font-family:"Josefin Sans",sans-serif;font-weight:600;color:var(--navy);text-transform:uppercase;white-space:nowrap;text-align:center;transform:translateX(-50%)}
  .line{position:absolute;white-space:nowrap}
  .center{transform:translateX(-50%);text-align:center}
  .ico{display:inline-block;width:1em;text-align:center;margin-right:4px;font-size:.9em}

  .sheet{left:50px;top:0;width:803px;height:1136px;background:var(--paper)}
  .sheet .brand{left:401px;top:168px;font-size:30px;letter-spacing:4px}
  .sheet .footer-text{left:401px;font-size:13px}

  .card-front{left:388px;top:279px;width:378px;height:222px;background:var(--paper)}
  .card-front .brand{left:86px;top:66px;font-size:13px;letter-spacing:1.5px}
  .agent-name{left:234px;top:36px;font-size:20px;font-weight:600;color:var(--navy)}
  .agent-role{left:234px;top:60px;font-size:12px;color:var(--ink)}
  .card-front .contact{left:17px;font-size:11px}

  .card-back{left:791px;top:279px;width:379px;height:222px;background:var(--navy)}
  .card-back .web{left:190px;top:191px;font-size:11px}

  .envelope{left:374px;top:522px;width:727px;height:440px}
  .envelope .brand{left:112px;top:192px;font-size:19px;line-height:24px;letter-spacing:2.5px}
  .envelope .band-text{left:344px;font-size:10px}
</style>
</head>
<body>

<section class="sheet" aria-label="Letterhead">
  <svg width="803" height="1136">
    <circle cx="401" cy="98" r="56" fill="none" stroke="var(--navy)" stroke-width="4"/>
    <rect x="0" y="1032" width="803" height="104" fill="var(--navy)"/>
    <circle cx="742" cy="1084" r="58" fill="var(--paper)"/>
    <circle cx="742" cy="1084" r="48" fill="var(--paper)" stroke="var(--navy)" stroke-width="5"/>
  </svg>
  <div class="brand">Harborline Realty</div>
  <div class="line center footer-text" style="top:1065px">Harborline Realty</div>
  <div class="line center footer-text" style="top:1092px">
    <span class="ico">☎</span>555-014-2288 &nbsp;<span class="ico">✉</span>info@harborline-realty.com &nbsp;<span class="ico">◍</span>www.harborline-realty.com
  </div>
</section>

<section class="card card-front" aria-label="Business card front">
  <svg width="378" height="222">
    <circle cx="86" cy="39" r="23" fill="none" stroke="var(--navy)" stroke-width="2.5"/>
    <rect x="0" y="111" width="378" height="111" fill="var(--navy)"/>
    <circle cx="320" cy="167" r="57" fill="var(--paper)"/>
    <circle cx="320" cy="167" r="48" fill="var(--paper)" stroke="var(--navy)" stroke-width="5"/>
  </svg>
  <div class="brand">Harborline Realty</div>
  <div class="line agent-name">Daniel Reyes</div>
  <div class="line agent-role">Realtor</div>
  <div class="line contact" style="top:125px"><span class="ico">⌂</span>Harborline Realty</div>
  <div class="line contact" style="top:157px"><span class="ico">☎</span>555-014-2288</div>
  <div class="line contact" style="top:173px"><span class="ico">✉</span>info@harborline-realty.com</div>
  <div class="line contact" style="top:189px"><span class="ico">◍</span>www.harborline-realty.com</div>
</section>

<section class="card card-back" aria-label="Business card back">
  <svg width="379" height="222">
    <circle cx="189" cy="114" r="27" fill="none" stroke="var(--paper)" stroke-width="3"/>
  </svg>
  <div class="line center web">www.harborline-realty.com</div>
</section>

<section class="envelope" aria-label="Envelope">
  <svg width="727" height="440">
    <path d="M0 96 L24 14 Q28 0 44 0 L683 0 Q699 0 703 14 L727 96 Z" fill="var(--navy)"/>
    <rect x="0" y="96" width="727" height="344" fill="var(--paper)"/>
    <circle cx="112" cy="150" r="34" fill="none" stroke="var(--navy)" stroke-width="3"/>
    <rect x="0" y="359" width="727" height="81" fill="var(--navy)"/>
    <circle cx="684" cy="400" r="44" fill="var(--paper)"/>
    <circle cx="684" cy="400" r="36" fill="var(--paper)" stroke="var(--navy)" stroke-width="4"/>
  </svg>
  <div class="brand">Harborline<br>Realty</div>
  <div class="line center band-text" style="top:384px">Harborline Realty</div>
  <div class="line center band-text" style="top:405px">
    <span class="ico">☎</span>555-014-2288 <span class="ico">✉</span>info@harborline-realty.com &nbsp;<span class="ico">◍</span>www.harborline-realty.com
  </div>
</section>

</body>
</html>
```